LB - WESITE NEEDED PAGE: Clean / Modern / Pro & Dynamic

Lantern-Brokers is a new insurance brokerage firm dealing exclusively with companies (BToB) providing the following property: Liabilities Insurance Insurances Automobile Insurance Insurances Construction% 26amp; Engineering Casualty Workmen 's Compensation Health Insurance Marime% 26amp; Transit Credit Insurance Young, Fast, Proactive and Dynamic we call ourselves Lantern-Brokers because we are a "start-up" willing to make a difference in the market, bringing modernity and speed to our industry, still too bureaucratic / procedural / opaque uninitiated. We need something respecting the colors of our orange logtype; blue; white; black; easy to scroll, with simple information on the company; - who we are - our team (with the pictures) - what we do - what we do - contact us, contact us (google map) Luanda (Angola) Small company, just need something flashy / professional / structured / modern.

Target Market(s)

BtoB; Oil and gas companies; French speaking copying established in Angola, all industrials, factories and importers of goods.

Industry/Entity Type

Insurance Broker

Font styles to use
Sans Serif

Colors

Designer to choose colors to be used in the design.

Requirements
Must have
• We need something respecting the colors of our orange logtype; blue; white; black; easy to scroll, with simple information on the company; - who we are - our team (with the pictures) - what we do - what we do - contact us, contact us (google map) Luanda (Angola) Small company, just need something flashy / professional / structured / modern.
Nice to have
• A page format
Should not have
• WE DO NOT WANT A REFER TO OUR LOGO, but a Home Page for our Website with the basics categories ... >> PLEASE CAREFULLY USE THE RIGHT COLOR OF THE LOGOTYPE which are the ones enclosed Orange / Turquoise / Black as per the business card .

```html
<!DOCTYPE html>
<html lang="en">
<head>
<meta charset="utf-8">
<title>Lantern-Brokers | Insurance Brokerage</title>
<link rel="stylesheet" href="https://fonts.googleapis.com/css2?family=Lato:ital,wght@0,400;0,700;0,900;1,400&family=Raleway:wght@400;500;600;700&display=swap">
<style>
:root{
  --blue:#2b8ff0;
  --red:#e8402b;
  --orange:#f07d2b;
  --ink:#333;
  --muted:#8a8a8a;
  --nav:#d6d6d6;
  --slate:#9ba6b3;
  --footer:#3d3f44;
  --footer-deep:#2e3034;
  --white:#fff;
}
*{margin:0;padding:0;box-sizing:border-box}
html,body{width:1200px;height:3895px;overflow:hidden}
body{position:relative;background:var(--white);font-family:"Lato",sans-serif;color:var(--ink)}
h1,h2,h3,h4,h5{font-weight:400}
.abs{position:absolute}
.btn{position:absolute;display:flex;align-items:center;justify-content:center;color:#fff;font-family:"Lato",sans-serif;font-size:10px;font-weight:700;letter-spacing:.3px;text-transform:uppercase}
.btn-blue{background:var(--blue)}
.btn-red{background:var(--red)}

/* header */
.site-header{position:absolute;left:0;top:0;width:1200px;height:68px;background:#fff}
.brand{position:absolute;left:150px;top:0;width:140px;height:68px;display:flex;align-items:center;gap:6px}
.brand-mark{width:9px;height:9px;background:var(--blue)}
.brand-name{color:var(--ink);font-weight:700;font-size:12px}
.top-contact{position:absolute;left:725px;font-size:9px;color:#7b8694;display:flex;align-items:center;gap:8px}
.main-nav{position:absolute;left:0;top:68px;width:1200px;height:35px;background:var(--nav)}
.nav-item{position:absolute;top:0;height:35px;display:flex;align-items:center;font-size:9.5px;font-weight:700;color:#333;text-transform:uppercase}
.nav-item.active{color:var(--red)}
.nav-sep{position:absolute;top:0;width:1px;height:35px;background:#c3c3c3}

/* hero */
.hero{position:absolute;left:0;top:103px;width:1200px;height:503px;background:linear-gradient(100deg,#cfe6ef 0%,#6fa7c2 30%,#2f5f83 55%,#6c8ea6 75%,#b6c6d2 100%)}
.hero-card{position:absolute;left:148px;top:308px;width:367px;height:247px;background:rgba(60,60,60,.93);padding:22px 29px}
.hero-card h1{font-family:"Raleway",sans-serif;font-weight:400;font-size:15px;line-height:32px;color:var(--blue)}
.hero-card p{font-size:10.5px;line-height:28px;color:#fff;margin-top:4px}

/* services */
.section-badge{position:absolute;left:533px;top:656px;width:108px;height:23px;background:var(--red);color:#fff;font-size:11px;font-weight:900;display:flex;align-items:center;justify-content:center}
.service{position:absolute;top:722px;width:220px;text-align:center}
.service h3{font-size:10.5px;font-weight:700;margin-top:18px;text-transform:uppercase}
.service p{font-size:10.5px;line-height:28px;color:var(--muted);margin-top:12px}

/* about & stats */
.about{position:absolute;left:0;top:973px;width:660px;height:470px;background:var(--blue)}
.stats{position:absolute;left:660px;top:973px;width:540px;height:470px;background:var(--red)}
.band-title{position:absolute;top:60px;font-family:"Raleway",sans-serif;font-weight:700;font-size:19px;color:#fff}
.band-rule{position:absolute;top:92px;width:47px;height:2px}
.about-copy{position:absolute;left:148px;top:153px;width:386px;font-size:8.4px;line-height:14px;font-weight:900;color:#fff;text-transform:uppercase;text-align:justify}
.stat{position:absolute;width:192px;height:93px;border:2px solid #fff;color:#fff;padding:24px 0 0 62px}
.stat strong{display:block;font-family:"Raleway",sans-serif;font-size:20px;font-weight:700}
.stat span{font-size:11px;font-weight:700}

/* getting started */
.started-title{position:absolute;left:0;top:1530px;width:1218px;text-align:center;font-family:"Raleway",sans-serif;font-weight:400;font-size:19px;color:#333}
.started-intro{position:absolute;left:280px;top:1596px;width:658px;text-align:center;font-size:10.5px;line-height:28px;color:var(--muted)}
.program-box{position:absolute;left:151px;top:1701px;width:911px;height:407px;border:1px solid #e4e4e4}
.program-divider{position:absolute;left:456px;top:0;width:1px;height:405px;background:#e4e4e4}
.program{position:absolute;top:0;width:455px;height:405px}
.program h3{position:absolute;left:100px;top:38px;font-family:"Raleway",sans-serif;font-weight:400;font-size:14px;text-transform:uppercase}
.program ul{position:absolute;left:55px;top:91px;width:385px;list-style:none}
.program li{position:relative;font-size:10.5px;line-height:28px;color:var(--muted);padding-left:11px;margin-bottom:27px}
.program li::before{content:"";position:absolute;left:0;top:12px;width:4px;height:4px;border-radius:50%;background:#999}

/* team */
.team-title{position:absolute;left:515px;top:2173px;width:174px;height:39px;background:var(--blue);color:#fff;font-family:"Raleway",sans-serif;font-weight:400;font-size:19px;display:flex;align-items:center;justify-content:center}
.member{position:absolute;top:2267px;width:212px}
.portrait{width:212px;height:203px}
.member h4{font-family:"Raleway",sans-serif;font-weight:500;font-size:13px;margin-top:20px}
.member em{display:block;font-size:10.5px;color:var(--orange);margin-top:8px}
.member p{font-size:10.5px;line-height:28px;color:var(--muted);margin-top:9px}
.socials{display:flex;margin-top:13px}
.socials i{display:block;width:27px;height:23px;border:1px solid #ddd;margin-right:-1px}

/* cta */
.cta-band{position:absolute;left:0;top:2770px;width:1200px;height:353px;background:var(--slate)}
.cta-card{position:absolute;left:263px;top:99px;width:648px;height:148px;background:#f4f5f7;text-align:center;padding-top:21px}
.cta-card p{font-family:"Raleway",sans-serif;font-size:14px;line-height:33px;color:#333}

/* map */
.map{position:absolute;left:0;top:3123px;width:1200px;height:434px;background:linear-gradient(90deg,#a5cbeb 0%,#a5cbeb 38%,#e9e7e2 60%,#e3e1dc 100%)}

/* footer */
.site-footer{position:absolute;left:0;top:3557px;width:1200px;height:287px;background:var(--footer)}
.footer-col{position:absolute;top:42px;width:220px;color:#d4d4d4}
.footer-col h5{font-family:"Raleway",sans-serif;font-size:12.5px;font-weight:600;color:#fff;padding-bottom:9px;border-bottom:2px solid var(--blue);display:inline-block;width:135px}
.footer-col p{font-size:10.5px;line-height:28px;margin-top:16px}
.tweet{position:relative;padding-left:24px;font-size:9.5px;line-height:22px;color:#fff;margin-top:14px}
.tweet a{color:var(--orange);text-decoration:none}
.tags{display:flex;flex-wrap:wrap;gap:12px 6px;width:215px;margin-top:20px}
.tags span{height:22px;background:#5a5d63;color:#a9acb2;font-size:8px;display:flex;align-items:center;justify-content:center;text-transform:uppercase}
.tags span.on{background:var(--blue);color:#fff}
.contact-line{font-size:10px;line-height:24.5px}
.contact-line b{color:#fff}
.footer-socials{display:flex;gap:12px;margin-top:16px}
.footer-socials i{width:22px;height:22px;border:1px solid #777}
.legal{position:absolute;left:0;top:3844px;width:1200px;height:51px;background:var(--footer-deep);font-size:9px;color:#9a9da3;padding:17px 0 0 148px}
</style>
</head>
<body>

<header class="site-header">
  <div class="brand"><span class="brand-mark"></span><span class="brand-name">Lantern-Brokers</span></div>
  <div class="top-contact" style="top:17px">
    <svg width="10" height="10" viewBox="0 0 10 10"><path d="M2 1l2 2-1 1.2c.6 1.3 1.5 2.2 2.8 2.8L7 6l2 2-1.3 1.3C4 9 1 6 .7 2.3z" fill="var(--blue)"/></svg>+244 900 000 111</div>
  <div class="top-contact" style="top:37px">
    <svg width="10" height="10" viewBox="0 0 10 10"><rect x="1" y="2" width="8" height="6" fill="var(--blue)"/></svg>hello@lantern-brokers.test</div>
  <div class="btn btn-blue" style="left:858px;top:23px;width:62px;height:22px">Login</div>
  <div class="btn btn-blue" style="left:934px;top:23px;width:94px;height:22px">Get a quote</div>
  <div class="btn btn-blue" style="left:1040px;top:23px;width:21px;height:22px">
    <svg width="11" height="11" viewBox="0 0 11 11"><circle cx="4.5" cy="4.5" r="3.3" fill="none" stroke="#fff" stroke-width="1.4"/><path d="M7 7l3 3" stroke="#fff" stroke-width="1.4"/></svg></div>
</header>

<nav class="main-nav">
  <span class="nav-sep" style="left:150px"></span>
  <span class="nav-item active" style="left:178px">Home &nbsp;⌄</span>
  <span class="nav-sep" style="left:240px"></span>
  <span class="nav-item" style="left:287px">Insurance &nbsp;&nbsp;&nbsp;&nbsp;⌄</span>
  <span class="nav-sep" style="left:385px"></span>
  <span class="nav-item" style="left:428px">Who we are &nbsp;&nbsp;&nbsp;&nbsp;⌄</span>
  <span class="nav-sep" style="left:535px"></span>
  <span class="nav-item" style="left:576px">Our team &nbsp;&nbsp;&nbsp;&nbsp;⌄</span>
  <span class="nav-sep" style="left:668px"></span>
  <span class="nav-item" style="left:700px">What we do</span>
  <span class="nav-sep" style="left:786px"></span>
  <span class="nav-item" style="left:820px">Contact us</span>
  <span class="nav-sep" style="left:900px"></span>
  <span class="nav-item" style="left:915px"><svg width="11" height="11" viewBox="0 0 11 11"><circle cx="2" cy="5.5" r="1.6" fill="#333"/><circle cx="9" cy="2" r="1.6" fill="#333"/><circle cx="9" cy="9" r="1.6" fill="#333"/><path d="M2 5.5L9 2M2 5.5L9 9" stroke="#333"/></svg></span>
  <span class="nav-sep" style="left:940px"></span>
</nav>

<section class="hero" role="img" aria-label="Photo of a businessman in a suit touching floating screens labelled liability and support"></section>
<div class="hero-card">
  <h1>Check our insurance services and get up to 25% off for you sign up.</h1>
  <p>Consetetur sadipscing elitr, sed diam nonumy eirmod tempor invidunt ut labore et dolore magna aliquyam erat, sed diam voluptua.</p>
</div>
<div class="btn btn-blue" style="left:178px;top:500px;width:106px;height:21px">Sign up today</div>

<div class="section-badge">OUR SERVICES</div>
<div class="service" style="left:132px">
  <svg width="30" height="36" viewBox="0 0 30 36"><circle cx="15" cy="10" r="7" fill="none" stroke="var(--red)" stroke-width="2"/><path d="M4 34v-6a11 8 0 0 1 22 0v6z" fill="none" stroke="var(--red)" stroke-width="2"/></svg>
  <h3>Our insurances</h3>
  <p>Consetetur sadipscing elitr, sed diam nonumy eirmod tempor invidunt ut labore et dolore magna aliquyam erat, sed diam voluptua.</p>
</div>
<div class="service" style="left:488px">
  <svg width="30" height="36" viewBox="0 0 30 36"><path d="M15 2a9 9 0 0 0-5 16.5V24h10v-5.5A9 9 0 0 0 15 2z" fill="none" stroke="var(--red)" stroke-width="2"/><path d="M11 28h8M12 32h6M15 12v8" stroke="var(--red)" stroke-width="2"/></svg>
  <h3>Offers</h3>
  <p>At vero eos et accusam et justo duo dolores et ea rebum. Stet clita kasd gubergren, no sea takimata sanctus est Lorem ipsum dolor sit amet.</p>
</div>
<div class="service" style="left:845px">
  <svg width="34" height="36" viewBox="0 0 34 36"><rect x="8" y="3" width="22" height="30" fill="none" stroke="var(--red)" stroke-width="2"/><path d="M3 9v24h5M13 10h12M13 16h12M13 22h12M13 28h8" stroke="var(--red)" stroke-width="2" fill="none"/></svg>
  <h3>Safe contracts</h3>
  <p>Consetetur sadipscing elitr, sed diam nonumy eirmod tempor invidunt ut labore et dolore magna aliquyam erat, sed diam voluptua.</p>
</div>

<section class="about">
  <h2 class="band-title" style="left:145px">WHO WE ARE?</h2>
  <span class="band-rule" style="left:145px;background:#fff"></span>
  <p class="about-copy">Lorem ipsum dolor sit amet, consectetur adipiscing elit, sed do eiusmod tempor incididunt ut labore et dolore magna aliqua. Quis ipsum suspendisse ultrices gravida. Risus commodo viverra maecenas accumsan lacus vel facilisis. Lorem ipsum dolor sit amet, consectetur adipiscing elit, sed do eiusmod tempor incididunt ut labore et dolore magna aliqua. Quis ipsum suspendisse ultrices gravida. Risus commodo viverra maecenas accumsan lacus vel facilisis. Lorem ipsum dolor sit amet, consectetur adipiscing elit, sed do eiusmod tempor incididunt ut labore et dolore magna aliqua. Quis ipsum suspendisse ultrices gravida. Risus commodo viverra maecenas accumsan lacus vel facilisis. Lorem ipsum dolor sit amet, consectetur adipiscing elit, sed do eiusmod tempor incididunt ut labore et dolore magna aliqua. Quis ipsum suspendisse ultrices gravida.</p>
  <div class="btn btn-red" style="left:423px;top:366px;width:117px;height:32px;font-size:11px">Read more</div>
</section>
<section class="stats">
  <h2 class="band-title" style="left:56px">STATISTICS COMPANY</h2>
  <span class="band-rule" style="left:56px;background:var(--blue)"></span>
  <div class="stat" style="left:56px;top:135px;padding-left:63px"><strong>10+</strong><span>Years Experience</span></div>
  <div class="stat" style="left:263px;top:135px;padding-left:63px"><strong>600+</strong><span>Complete Projects</span></div>
  <div class="stat" style="left:56px;top:243px;padding-left:63px"><strong>15+</strong><span>Awards Received</span></div>
  <div class="stat" style="left:263px;top:243px;padding-left:63px"><strong>600+</strong><span>Complete Projects</span></div>
  <div class="btn btn-blue" style="left:56px;top:366px;width:117px;height:32px;font-size:11px">Get a quote</div>
</section>

<h2 class="started-title">HOW TO GET STARTED</h2>
<p class="started-intro">Lorem ipsum dolor sit amet, consetetur sadipscing elitr, sed diam nonumy eirmod tempor invidunt ut labore et dolore magna aliquyam erat, sed diam voluptua.</p>
<div class="program-box">
  <div class="program" style="left:0">
    <svg class="abs" style="left:38px;top:30px" width="34" height="32" viewBox="0 0 34 32"><rect x="2" y="10" width="18" height="18" fill="none" stroke="var(--red)" stroke-width="2"/><path d="M6 16h10M6 21h10M20 12l8-8 4 4-8 8M24 4l-2-2" stroke="var(--red)" stroke-width="2" fill="none"/></svg>
    <h3>Insurance programs</h3>
    <ul>
      <li>Lorem ipsum dolor sit amet, consetetur sadipscing elitr, sed diam nonumy eirmod tempor invidunt ut labore et dolore magna</li>
      <li>Consetetur sadipscing elitr, sed diam nonumy eirmod tempor invidunt ut labore et dolore magna aliquyam erat, sed diam voluptua.</li>
      <li>At vero eos et accusam et justo duo dolores et ea rebum. Stet clita kasd gubergren, no sea takimata sanctus est Lorem ipsum dolor sit amet.</li>
    </ul>
    <div class="btn btn-red" style="left:44px;top:353px;width:94px;height:23px">View details</div>
  </div>
  <span class="program-divider"></span>
  <div class="program" style="left:456px">
    <svg class="abs" style="left:26px;top:30px" width="30" height="34" viewBox="0 0 30 34"><path d="M4 2v31" stroke="var(--red)" stroke-width="2.5"/><path d="M5 4h12v4h10v12H15v-4H5" fill="none" stroke="var(--red)" stroke-width="2"/></svg>
    <h3 style="left:80px">How we can help you</h3>
    <ul style="left:36px">
      <li>Lorem ipsum dolor sit amet, consetetur sadipscing elitr, sed diam nonumy eirmod tempor invidunt ut labore et dolore magna</li>
      <li>Consetetur sadipscing elitr, sed diam nonumy eirmod tempor invidunt ut labore et dolore magna aliquyam erat, sed diam voluptua.</li>
      <li>At vero eos et accusam et justo duo dolores et ea rebum. Stet clita kasd gubergren, no sea takimata sanctus est Lorem ipsum dolor sit amet.</li>
    </ul>
    <div class="btn btn-red" style="left:31px;top:353px;width:94px;height:23px">View details</div>
  </div>
</div>

<h2 class="team-title">MEET OUR TEAM</h2>
<article class="member" style="left:148px">
  <div class="portrait" role="img" aria-label="Portrait photo of Clara Mendes" style="background:linear-gradient(160deg,#6f86a6,#9a7a66)"></div>
  <h4>Clara Mendes</h4><em>CEO / Employee Manager</em>
  <p>Stet clita kasd gubergren, no sea takimata sanctus est Lorem ipsum dolor sit amet. Lorem ipsum dolor sit amet, consetetur sadipscing elitr</p>
  <div class="socials"><i></i><i></i><i></i><i></i></div>
</article>
<article class="member" style="left:382px">
  <div class="portrait" role="img" aria-label="Portrait photo of Helena Voss" style="background:linear-gradient(160deg,#8faa6c,#d9c7a8)"></div>
  <h4>Helena Voss</h4><em>Head Office Manager</em>
  <p>Stet clita kasd gubergren, no sea takimata sanctus est Lorem ipsum dolor sit amet. Lorem ipsum dolor sit amet, consetetur sadipscing elitr</p>
  <div class="socials"><i></i><i></i><i></i><i></i></div>
</article>
<article class="member" style="left:616px">
  <div class="portrait" role="img" aria-label="Portrait photo of Marc Duval" style="background:linear-gradient(180deg,#2c2f36,#2c3d5e)"></div>
  <h4>Marc Duval</h4><em>Insurance Manager</em>
  <p>Stet clita kasd gubergren, no sea takimata sanctus est Lorem ipsum dolor sit amet. Lorem ipsum dolor sit amet, consetetur sadipscing elitr</p>
  <div class="socials"><i></i><i></i><i></i><i></i></div>
</article>
<article class="member" style="left:851px">
  <div class="portrait" role="img" aria-label="Portrait photo of Tomas Reyes" style="background:linear-gradient(160deg,#b59a86,#e6e3de)"></div>
  <h4>Tomas Reyes</h4><em>Marketing Assistant</em>
  <p>Stet clita kasd gubergren, no sea takimata sanctus est Lorem ipsum dolor sit amet. Lorem ipsum dolor sit amet, consetetur sadipscing elitr</p>
  <div class="socials"><i></i><i></i><i></i><i></i></div>
</article>

<section class="cta-band">
  <div class="cta-card">
    <p>Lorem ipsum dolor sit amet, consetetur sadipscing elitr, sed diam nonumy eirmod<br>tempor invidunt ut labore et dolore magna aliquyam erat, sed diam voluptua.</p>
    <div class="btn btn-blue" style="left:272px;top:102px;width:106px;height:21px">Sign up today</div>
  </div>
</section>

<section class="map" role="img" aria-label="Street map of Luanda, Angola, showing the office location"></section>

<footer class="site-footer">
  <div class="footer-col" style="left:148px">
    <h5>About Us</h5>
    <p>At vero eos et accusam et justo duo dolores et ea rebum. Stet clita kasd gubergren, no sea takimata sanctus est lorem ipsum dolor sit amet.</p>
  </div>
  <div class="footer-col" style="left:382px">
    <h5>News Feed</h5>
    <div class="tweet" style="margin-top:18px"><svg class="abs" style="left:2px;top:6px" width="10" height="9" viewBox="0 0 10 9"><path d="M1 2l8 2.5L1 7z" fill="var(--blue)"/></svg>Check out our insurance programs here<br><a>@lb.test/news</a></div>
    <div class="tweet" style="margin-top:20px"><svg class="abs" style="left:2px;top:6px" width="10" height="9" viewBox="0 0 10 9"><path d="M1 2l8 2.5L1 7z" fill="var(--blue)"/></svg>We are an insurance group with high quality requirements <a>@lb.test/news</a></div>
  </div>
  <div class="footer-col" style="left:616px">
    <h5>Popular Categories</h5>
    <div class="tags">
      <span style="width:81px">Contract</span><span class="on" style="width:74px">Trends</span>
      <span style="width:81px">Security</span><span style="width:65px">Store</span><span style="width:50px">Safe</span>
      <span style="width:43px">Top</span><span style="width:65px">Shirt</span><span style="width:72px">Secure</span>
      <span style="width:93px">Insurance</span><span style="width:84px">Payments</span>
    </div>
  </div>
  <div class="footer-col" style="left:851px">
    <h5>Contact Us</h5>
    <div style="margin-top:14px">
      <div class="contact-line">12 Rua Marginal, Luanda -<br>Angola</div>
      <div class="contact-line"><b>Phone:</b> (244) 0222 3344 556</div>
      <div class="contact-line"><b>E-mail:</b> contact@lantern-brokers.test</div>
    </div>
    <div class="footer-socials"><i></i><i></i><i></i><i></i><i></i><i></i></div>
  </div>
</footer>
<div class="legal">© 2015 &nbsp;&nbsp;&nbsp;&nbsp;|&nbsp;&nbsp; All rights reserved</div>

</body>
</html>
```